New Business Card Design Project

We require a business card design for Vexalund, a newly established Indian company.
Our focus is on the development, manufacturing, and export of a diverse array of pharmaceutical products on a global scale. The card should convey a professional appearance, as our primary markets are in Africa, China, and Southeast Asian nations.
We envision a two-sided business card, with the reverse side dedicated to a logo set against a solid color or an elegantly designed pattern. The corners should be rounded. We would appreciate seeing both horizontal and vertical design options. We trust the designer to utilize their expertise in creating this design.

The content for the business card is included in the attached Word file.

Target Market(s)

Our primary markets are in Africa, China, and Southeast Asian, Latin America, Maldives, Sri Lanka

Industry/Entity Type

Pharmaceutical Manufacturing and Export

Contact Information for Business Card

Colors

Designer to choose colors to be used in the design.

Requirements
Must have
• The reverse side of the business card features solely the logo along with the tagline, "Remedies of Life."
Should not have
• The logo should not exceed two instances, encompassing both the front and back sides of the card.

```html
<!DOCTYPE html>
<html lang="en">
<head>
<meta charset="utf-8">
<title>Vexalund Business Card</title>
<link rel="stylesheet" href="https://fonts.googleapis.com/css2?family=Montserrat:wght@700&family=Open+Sans:wght@300;400&display=swap">
<style>
  :root {
    --bg: #232323;
    --card: #ffffff;
    --blue: #2ea8df;
    --coral: #ef634d;
    --ink: #1d1d1d;
  }
  * { margin: 0; padding: 0; box-sizing: border-box; }
  html, body { width: 1200px; height: 711px; overflow: hidden; background: var(--bg); }
  .stage { position: relative; width: 1200px; height: 711px; }

  .card {
    position: absolute;
    top: 96px;
    width: 300px;
    height: 520px;
    background: var(--card);
    border-radius: 22px;
    box-shadow: -6px 6px 0 var(--blue), -10px 16px 28px rgba(0,0,0,.55);
    overflow: hidden;
  }
  .card-back { left: 262px; }
  .card-front { left: 642px; }

  /* Back side */
  .back-mark {
    position: absolute;
    left: 50%; top: 50%;
    transform: translate(-50%, -50%) rotate(90deg);
    display: flex;
    flex-direction: column;
    align-items: center;
    gap: 10px;
  }
  .brand {
    display: flex;
    align-items: center;
    gap: 10px;
    font-family: "Montserrat", sans-serif;
    font-weight: 700;
    color: var(--blue);
    letter-spacing: .5px;
  }
  .brand-dot { border-radius: 50%; background: var(--coral); flex: none; }
  .back-mark .brand { font-size: 52px; }
  .back-mark .brand-dot { width: 26px; height: 26px; }
  .tagline {
    font-family: "Open Sans", sans-serif;
    font-size: 13px;
    color: var(--ink);
    letter-spacing: 1.5px;
  }

  /* Front side */
  .front-brand {
    position: absolute;
    top: 64px; left: 0; right: 0;
    justify-content: center;
    font-size: 34px;
  }
  .front-brand .brand-dot { width: 16px; height: 16px; }

  .contact-block {
    position: absolute;
    left: 48px; bottom: 62px;
    font-family: "Open Sans", sans-serif;
    color: var(--ink);
  }
  .person-name {
    font-size: 23px;
    color: var(--blue);
    white-space: nowrap;
  }
  .person-name .first { font-family: "Montserrat", sans-serif; font-weight: 700; }
  .person-name .last { font-weight: 300; }
  .person-role {
    font-family: "Montserrat", sans-serif;
    font-weight: 700;
    font-size: 12px;
    margin: 2px 0 16px 98px;
  }
  .address { font-size: 11.5px; line-height: 1.45; margin-bottom: 14px; }
  .contact-list { list-style: none; font-size: 12px; line-height: 1.7; }
  .contact-list li { display: flex; align-items: center; gap: 8px; }
  .contact-list svg { width: 12px; height: 12px; flex: none; }
</style>
</head>
<body>
<main class="stage">
  <section class="card card-back" aria-label="Card reverse">
    <div class="back-mark">
      <div class="brand"><span class="brand-dot"></span>Vexalund</div>
      <p class="tagline">Remedies of Life.</p>
    </div>
  </section>

  <section class="card card-front" aria-label="Card front">
    <div class="brand front-brand"><span class="brand-dot"></span>Vexalund</div>

    <div class="contact-block">
      <p class="person-name"><span class="first">Ravin</span> <span class="last">K. Tolmar</span></p>
      <p class="person-role">CEO</p>
      <p class="address">14, Kesar Colony,<br>Nandpur, 440917, India</p>
      <ul class="contact-list">
        <li>
          <svg viewBox="0 0 12 12" aria-hidden="true"><rect x="3" y="1" width="6" height="10" rx="1" fill="none" stroke="var(--coral)" stroke-width="1.2"/></svg>
          +919 400510372
        </li>
        <li>
          <svg viewBox="0 0 12 12" aria-hidden="true"><circle cx="6" cy="6" r="5" fill="var(--blue)"/><path d="M1 6h10M6 1c2 2 2 8 0 10M6 1c-2 2-2 8 0 10" stroke="#fff" stroke-width=".8" fill="none"/></svg>
          www.vexalund.com
        </li>
        <li>
          <svg viewBox="0 0 12 12" aria-hidden="true"><rect x="1" y="3" width="10" height="7" fill="var(--coral)"/><path d="M1 3l5 4 5-4" stroke="#fff" stroke-width=".9" fill="none"/></svg>
          rtolmar@vexalund.com
        </li>
      </ul>
    </div>
  </section>
</main>
</body>
</html>
```